Building Referrer Relationships Booklet

4 page A4 booklet to give to potential professional referrers to establish a collaborative relationship.Needs to be bright, vibrant, colourful, friendly, inviting, in keeping with The Linden Practice colours.
Want to provide potential referrer partners a great reason to choose to collaborate with us. They need to know who we are, what makes us different/appealing, and who we are looking for to connect with.
The final product should communicate high performance and connectedness.
Updates

Target Market(s)

professional medical allied health and fitness practitioners

Industry/Entity Type

Health

Requirements
Must have
• energetic, vibrant, engaging, inviting, images

```html
<!DOCTYPE html>
<html lang="en">
<head>
<meta charset="utf-8">
<title>Referral Partnerships – The Linden Practice</title>
<link rel="stylesheet" href="https://fonts.googleapis.com/css2?family=Raleway:wght@300;400;700;800;900&display=swap">
<style>
  :root {
    --backdrop: #8a8a8a;
    --paper: #ffffff;
    --brand-blue: #0b4f9c;
    --blue-light: #0a6cc0;
    --blue-deep: #203f9c;
    --brand-orange: #f28a1e;
    --orange-deep: #e8541a;
    --ink: #2b2b2b;
    --rule-grey: #d6d8dc;
    --wood-light: #e6cfb2;
    --wood-mid: #d2ad86;
    --skin-warm: #b9825c;
    --shade-dark: #4a3a32;
    --denim: #6f87a3;
  }
  * { margin: 0; padding: 0; box-sizing: border-box; }
  html, body {
    width: 903px; height: 1200px; overflow: hidden;
    background: var(--backdrop);
    font-family: "Raleway", sans-serif;
  }
  .booklet-cover {
    position: absolute; left: 95px; top: 97px;
    width: 708px; height: 1001px;
    background: var(--paper);
    overflow: hidden;
  }
  .cover-shapes { position: absolute; inset: 0; }
  .cover-title {
    position: absolute; left: 53px; top: 54px;
    color: var(--brand-blue);
    font-weight: 800; font-size: 51px; line-height: 56px;
  }
  .cover-tagline {
    position: absolute; left: 53px; top: 171px;
    color: var(--ink);
    font-weight: 400; font-size: 25px;
  }
  .brand-mark {
    position: absolute; left: 498px; top: 98px; width: 180px;
    display: flex; flex-direction: column; align-items: center;
  }
  .brand-mark-circle {
    width: 112px; height: 112px; border-radius: 50%;
    background: var(--brand-blue);
  }
  .brand-mark-name {
    margin-top: 14px;
    color: var(--brand-blue);
    font-weight: 700; font-size: 19px; white-space: nowrap;
  }
  .cover-message {
    position: absolute; right: 44px; top: 778px;
    text-align: right; color: var(--paper);
  }
  .cover-headline {
    font-weight: 900; font-size: 37px; line-height: 41px;
    text-shadow: 2px 2px 2px rgba(10, 25, 70, 0.85);
  }
  .cover-headline .highlight { color: var(--brand-orange); }
  .cover-body {
    margin-top: 16px;
    font-weight: 300; font-size: 27px; line-height: 32px;
  }
</style>
</head>
<body>
  <main class="booklet-cover">
    <svg class="cover-shapes" width="708" height="1001" viewBox="0 0 708 1001">
      <defs>
        <linearGradient id="swoosh-gradient" x1="0" x2="1" y1="0" y2="0">
          <stop offset="0" stop-color="var(--brand-orange)"/>
          <stop offset="1" stop-color="var(--orange-deep)"/>
        </linearGradient>
        <linearGradient id="wood-gradient" x1="0" x2="1" y1="0" y2="1">
          <stop offset="0" stop-color="var(--wood-mid)"/>
          <stop offset="1" stop-color="var(--wood-light)"/>
        </linearGradient>
        <radialGradient id="shade-upper-left" cx="0.1" cy="0.15" r="0.55">
          <stop offset="0" stop-color="var(--shade-dark)" stop-opacity="0.75"/>
          <stop offset="1" stop-color="var(--shade-dark)" stop-opacity="0"/>
        </radialGradient>
        <radialGradient id="shade-upper-mid" cx="0.42" cy="0.08" r="0.3">
          <stop offset="0" stop-color="var(--denim)" stop-opacity="0.6"/>
          <stop offset="1" stop-color="var(--denim)" stop-opacity="0"/>
        </radialGradient>
        <radialGradient id="warm-center" cx="0.45" cy="0.52" r="0.4">
          <stop offset="0" stop-color="var(--skin-warm)" stop-opacity="0.85"/>
          <stop offset="1" stop-color="var(--skin-warm)" stop-opacity="0"/>
        </radialGradient>
        <radialGradient id="shade-lower-left" cx="0.05" cy="0.95" r="0.4">
          <stop offset="0" stop-color="var(--shade-dark)" stop-opacity="0.7"/>
          <stop offset="1" stop-color="var(--shade-dark)" stop-opacity="0"/>
        </radialGradient>
        <linearGradient id="panel-gradient" x1="0" x2="1" y1="0" y2="0">
          <stop offset="0" stop-color="var(--blue-light)"/>
          <stop offset="1" stop-color="var(--blue-deep)"/>
        </linearGradient>
        <clipPath id="photo-clip">
          <path d="M0,308 C200,272 450,286 708,412 L708,1001 L0,1001 Z"/>
        </clipPath>
      </defs>
      <path class="orange-swoosh" fill="url(#swoosh-gradient)"
            d="M0,252 C200,236 450,246 708,398 L708,408 C450,272 200,258 0,296 Z"/>
      <g class="team-photo" role="img" clip-path="url(#photo-clip)"
         aria-label="Photo: a group of people stacking their hands together in the middle, seen from above on a wooden floor">
        <rect x="0" y="270" width="708" height="731" fill="url(#wood-gradient)"/>
        <rect x="0" y="270" width="708" height="731" fill="url(#shade-upper-left)"/>
        <rect x="0" y="270" width="708" height="731" fill="url(#shade-upper-mid)"/>
        <rect x="0" y="270" width="708" height="731" fill="url(#warm-center)"/>
        <rect x="0" y="270" width="708" height="731" fill="url(#shade-lower-left)"/>
      </g>
      <path class="divider-band" fill="var(--paper)"
            d="M0,790 C200,714 450,676 708,672 L708,700 C450,706 200,740 0,812 Z"/>
      <path class="divider-line" fill="var(--rule-grey)"
            d="M0,802 C200,726 450,690 708,686 L708,700 C450,706 200,740 0,812 Z"/>
      <path class="message-panel" fill="url(#panel-gradient)"
            d="M0,812 C200,740 450,706 708,700 L708,1001 L0,1001 Z"/>
    </svg>

    <h1 class="cover-title">Referral<br>Partnerships</h1>
    <p class="cover-tagline">Because Together We Achieve More</p>

    <div class="brand-mark">
      <span class="brand-mark-circle"></span>
      <span class="brand-mark-name">The Linden Practice</span>
    </div>

    <section class="cover-message">
      <h2 class="cover-headline">We are here to help our<br>clients <span class="highlight">get back on their feet.</span></h2>
      <p class="cover-body">Let’s combine our skillsets so<br>we can achieve even better results.</p>
    </section>
  </main>
</body>
</html>
```